Business Card Design for Occupational Medicine Start Up Company

We need to design a professional business card. We are a healthcare company providing occupational medicine services to blue collar industries. We are professional, efficient and high quality service providers.

Target Market(s)

Blue Collar Industry: Shipbuilding, Ports, Trucking Companies; The Executives and Safety Officers for these companies

Industry/Entity Type

Healthcare

Contact Information for Business Card

Logo, Name, Title, Email, Phone

Other font styles liked:
• Please match our Brand Guide

Requirements
Must have
• Our Company Colors and Logo

```html
<!DOCTYPE html>
<html lang="en">
<head>
<meta charset="utf-8">
<title>CrewCare Clinics – Business Card</title>
<link href="https://fonts.googleapis.com/css2?family=Montserrat:wght@400;500;600;700&display=swap" rel="stylesheet">
<style>
  :root {
    --backdrop: #2b2b2b;
    --paper: #f4f4f2;
    --navy: #2f2f72;
    --sky: #2a9ad6;
    --amber: #f0a830;
    --white: #ffffff;
  }
  * { margin: 0; padding: 0; box-sizing: border-box; }
  html, body {
    width: 1200px; height: 1200px; overflow: hidden;
    background: var(--backdrop);
    font-family: "Montserrat", sans-serif;
  }
  .canvas { position: relative; width: 1200px; height: 1200px; }
  .card {
    position: absolute;
    left: 300px;
    width: 594px;
    height: 348px;
    background: var(--paper);
    border-radius: 20px;
    overflow: hidden;
  }
  .card--front { top: 200px; }
  .card--back { top: 637px; }

  /* Front */
  .front-brand {
    position: absolute; left: 0; right: 0; top: 126px;
    display: flex; align-items: center; justify-content: center; gap: 14px;
  }
  .brand-dot {
    width: 26px; height: 26px; border-radius: 50%;
    background: var(--navy);
  }
  .brand-name {
    font-size: 34px; font-weight: 600; color: var(--navy);
    letter-spacing: 0.5px;
  }
  .front-web {
    position: absolute; left: 0; right: 0; top: 298px;
    text-align: center; font-size: 15px; font-weight: 500;
    letter-spacing: 1px; color: var(--navy);
  }

  /* Back */
  .back-shape { position: absolute; inset: 0; }
  .back-brand {
    position: absolute; left: 0; width: 300px; top: 0; height: 348px;
    display: flex; align-items: center; justify-content: center; gap: 10px;
  }
  .back-brand .brand-dot { background: var(--white); width: 20px; height: 20px; }
  .back-brand .brand-name { color: var(--white); font-size: 24px; }

  .holder {
    position: absolute; right: 31px; top: 38px; text-align: right;
  }
  .holder-name {
    font-size: 24px; font-weight: 600; color: var(--sky); letter-spacing: 0.5px;
    line-height: 1.1;
  }
  .holder-title {
    font-size: 15px; font-weight: 500; color: var(--navy); margin-top: 4px;
  }
  .address {
    position: absolute; right: 31px; top: 205px; text-align: right;
    font-size: 15px; font-weight: 500; color: var(--navy); line-height: 21px;
  }
  .contacts {
    position: absolute; right: 31px; top: 254px; list-style: none;
  }
  .contacts li {
    display: flex; align-items: center; justify-content: flex-end; gap: 12px;
    font-size: 15px; font-weight: 500; color: var(--navy); line-height: 22px;
  }
  .contacts svg { width: 14px; height: 14px; flex: none; }
</style>
</head>
<body>
<main class="canvas">
  <section class="card card--front" aria-label="Card front">
    <div class="front-brand">
      <span class="brand-dot"></span>
      <span class="brand-name">CrewCare Clinics</span>
    </div>
    <p class="front-web">www.crewcareclinics.com</p>
  </section>

  <section class="card card--back" aria-label="Card back">
    <svg class="back-shape" viewBox="0 0 594 348" preserveAspectRatio="none" aria-hidden="true">
      <path d="M238 0 Q370 174 240 348" fill="none" stroke="var(--amber)" stroke-width="6"/>
      <path d="M0 0 H232 Q362 174 232 348 H0 Z" fill="var(--navy)"/>
    </svg>
    <div class="back-brand">
      <span class="brand-dot"></span>
      <span class="brand-name">CrewCare Clinics</span>
    </div>

    <div class="holder">
      <h1 class="holder-name">DANA REYES</h1>
      <p class="holder-title">Senior Doctor</p>
    </div>

    <address class="address" style="font-style:normal">
      48 Harbor Lane, Suite 210<br>
      Portside, State 54321
    </address>

    <ul class="contacts">
      <li>555-014-2290
        <svg viewBox="0 0 14 14" aria-label="Phone"><path d="M1 5 Q7 0 13 5 L11 7 L9 5.5 V4.5 Q7 3.8 5 4.5 V5.5 L3 7 Z M3 8 H11 V12 H3 Z" fill="var(--sky)"/></svg>
      </li>
      <li>dana@crewcareclinics.com
        <svg viewBox="0 0 14 14" aria-label="Email"><rect x="1" y="3" width="12" height="8" fill="var(--navy)"/><path d="M1 3 L7 8 L13 3 M1 11 L5.5 7 M13 11 L8.5 7" stroke="var(--paper)" stroke-width="1" fill="none"/></svg>
      </li>
      <li>www.crewcare.com
        <svg viewBox="0 0 14 14" aria-label="Website"><circle cx="7" cy="7" r="6" fill="var(--amber)"/><path d="M1 7 H13 M7 1 V13 M2.5 4 H11.5 M2.5 10 H11.5" stroke="var(--paper)" stroke-width="0.8"/><ellipse cx="7" cy="7" rx="2.8" ry="6" fill="none" stroke="var(--paper)" stroke-width="0.8"/></svg>
      </li>
    </ul>
  </section>
</main>
</body>
</html>
```